Business card for a new cabinet shop company named Veloran Cabinets for high end cabinets

Design a business card, thinking dark rich green with colours to speak of high end luxury ie; cream, gold, black possibly

Mitchell Tarrowby
Director Craftsman
Email: info@veloranjoinery-example.com.au
Instagram : @veloran.cabinets

```html
<!DOCTYPE html>
<html lang="en">
<head>
<meta charset="UTF-8">
<title>Veloran Cabinets – Business Card</title>
<link href="https://fonts.googleapis.com/css2?family=Montserrat:wght@300;400;500;800&display=swap" rel="stylesheet">
<style>
  :root {
    --stage: #262626;
    --card: #0f241a;
    --card-raised: #163325;
    --grain-light: #1e3f2f;
    --gold: #c9a866;
    --gold-soft: #a88c55;
    --ivory: #f4f1ea;
  }
  * { box-sizing: border-box; margin: 0; padding: 0; }
  html, body {
    width: 1200px;
    height: 875px;
    overflow: hidden;
    background: var(--stage);
    font-family: "Montserrat", sans-serif;
  }
  .canvas {
    width: 1200px;
    height: 875px;
    display: flex;
    align-items: center;
    justify-content: center;
    gap: 40px;
  }
  .card {
    position: relative;
    width: 540px;
    height: 309px;
    background: var(--card);
    border-radius: 18px;
    overflow: hidden;
    box-shadow: 0 18px 40px rgba(0,0,0,.55);
  }
  .card__grain {
    position: absolute;
    left: 0;
    top: 0;
    width: 130px;
    height: 100%;
    background: linear-gradient(90deg, var(--card) 0%, var(--grain-light) 45%, var(--card) 100%);
    opacity: .85;
  }
  .brand {
    position: absolute;
    display: flex;
    align-items: center;
    color: var(--gold);
    font-weight: 500;
    white-space: nowrap;
  }
  .brand__mark {
    border: 2px solid var(--gold);
    flex: none;
  }
  /* Front */
  .card--front .brand {
    left: 50%;
    top: 50%;
    transform: translate(-50%, -50%);
    gap: 22px;
    font-size: 38px;
    letter-spacing: .02em;
  }
  .card--front .brand__mark { width: 54px; height: 54px; }
  /* Back */
  .card--back .brand {
    left: 44px;
    top: 112px;
    gap: 12px;
    font-size: 20px;
  }
  .card--back .brand__mark { width: 28px; height: 28px; }
  .emboss-panel {
    position: absolute;
    right: 52px;
    top: 108px;
    width: 120px;
    height: 120px;
    background: var(--card-raised);
    border-radius: 4px;
  }
  .person {
    position: absolute;
    right: 40px;
    top: 36px;
    text-align: right;
  }
  .person__name {
    font-size: 21px;
    line-height: 1.1;
  }
  .person__first { color: var(--ivory); font-weight: 800; }
  .person__last { color: var(--gold-soft); font-weight: 300; }
  .person__role {
    color: var(--ivory);
    font-size: 11px;
    font-weight: 400;
    margin-top: 4px;
    letter-spacing: .02em;
  }
  .contact {
    position: absolute;
    left: 44px;
    bottom: 34px;
    list-style: none;
    color: var(--ivory);
    font-size: 12.5px;
    font-weight: 400;
  }
  .contact__item {
    display: flex;
    align-items: center;
    gap: 10px;
    margin-top: 8px;
  }
  .contact__icon { flex: none; width: 14px; height: 14px; }
</style>
</head>
<body>
  <main class="canvas">
    <section class="card card--front" aria-label="Business card front">
      <div class="card__grain" role="img" aria-label="Raised gloss grain texture along the card edge"></div>
      <div class="brand">
        <span class="brand__mark"></span>
        <span class="brand__name">Veloran Cabinets</span>
      </div>
    </section>

    <section class="card card--back" aria-label="Business card back">
      <div class="card__grain" role="img" aria-label="Raised gloss grain texture along the card edge"></div>
      <div class="person">
        <p class="person__name"><span class="person__first">Mitchell</span> <span class="person__last">Tarrowby</span></p>
        <p class="person__role">Director Craftsman</p>
      </div>
      <div class="brand">
        <span class="brand__mark"></span>
        <span class="brand__name">Veloran Cabinets</span>
      </div>
      <div class="emboss-panel" role="img" aria-label="Tone-on-tone raised gloss panel"></div>
      <ul class="contact">
        <li class="contact__item">
          <svg class="contact__icon" viewBox="0 0 14 14" aria-hidden="true">
            <rect x="1" y="3" width="12" height="8" fill="var(--gold)"/>
            <path d="M1 3 L7 8 L13 3" fill="none" stroke="var(--card)" stroke-width="1.2"/>
          </svg>
          <span>info@veloranjoinery-example.com.au</span>
        </li>
        <li class="contact__item">
          <svg class="contact__icon" viewBox="0 0 14 14" aria-hidden="true">
            <circle cx="7" cy="7" r="6" fill="var(--gold)"/>
          </svg>
          <span>@veloran.cabinets</span>
        </li>
      </ul>
    </section>
  </main>
</body>
</html>
```